Modern Medical Optometry Website

We need mordern, Patient friendly website. Easy to navigate and enhance our advance medical technology and excellent patient care.
1. HOME PAGE
2. OUR TEAM PAGE
3. EYECARE PAGE - VISION SERVICES, EYE EXAMS, KERATOCONUS CENTER, GLAUCOMA , DIABITES, MELORIDEX EXAM, DIGITAL RETINAL, OCT.
4. MYOPIA CONTROL CLINIC
5. DRY EYE CLINIC
6. EYEWEAR
7. PATIENT CENTER - BLOG
7. CONTACT US
This is our current website www.brivaloka.com
and We want to add more content and a cleaner design like these website
http://tarnwickfolvendale.com/
https://www.qmvorlu.com/

```html
<!DOCTYPE html>
<html lang="en">
<head>
<meta charset="utf-8">
<title>Lumavue Optometry</title>
<link href="https://fonts.googleapis.com/css2?family=Poppins:ital,wght@0,400;0,500;0,600;0,700;1,400;1,500&display=swap" rel="stylesheet">
<style>
:root{
  --blue:#2f74bd;
  --blue-deep:#2a5fa6;
  --navy:#163a6b;
  --teal:#1b86b3;
  --yellow:#f6c515;
  --ink:#1f1f1f;
  --body:#444;
  --light:#eef1f5;
  --footer:#0d0d0d;
  --white:#fff;
}
*{margin:0;padding:0;box-sizing:border-box}
html,body{width:1200px;height:4523px;overflow:hidden}
body{font-family:'Poppins',sans-serif;color:var(--body);background:var(--white);position:relative}
.abs{position:absolute}
p{font-size:15px;line-height:26px}

/* header */
.header{left:0;top:0;width:1200px;height:157px;background:var(--white)}
.logo{left:150px;top:38px;display:flex;align-items:center;gap:12px}
.logo-box{width:46px;height:46px;background:var(--yellow)}
.logo-name{font-size:18px;font-weight:600;color:var(--navy);line-height:20px}
.call{left:573px;top:24px;display:flex;align-items:center;gap:12px}
.call-icon{width:40px;height:40px;border-radius:50%;border:2px solid var(--blue);display:flex;align-items:center;justify-content:center}
.call small{display:block;font-size:15px;color:var(--ink);line-height:18px}
.call strong{display:block;font-size:24px;color:var(--navy);font-weight:700;line-height:28px}
.btn-yellow{background:var(--yellow);color:var(--ink);font-weight:600;font-size:14px;border-radius:24px;display:flex;align-items:center;justify-content:center;gap:8px;text-transform:uppercase}
.header .btn-yellow{left:820px;top:24px;width:235px;height:48px}
.nav{left:286px;top:108px;width:914px;height:49px;background:var(--blue);clip-path:polygon(30px 0,100% 0,100% 100%,0 100%)}
.nav ul{list-style:none;display:flex;gap:26px;padding-left:50px;height:49px;align-items:center}
.nav li{color:var(--white);font-size:15px}

/* hero */
.hero{left:0;top:157px;width:1200px;height:673px;background:linear-gradient(100deg,#1d4d8c 0%,#3b7fc4 45%,#8fb4d6 75%,#c9d7e4 100%)}
.hero-photo{left:560px;top:0;width:640px;height:673px;background:radial-gradient(circle at 55% 40%,#3e6fa5 0,#6d93bb 30%,#b9c8d8 65%,rgba(200,212,225,0) 100%)}
.hero h1{left:127px;top:176px;font-size:42px;font-weight:700;color:var(--white);letter-spacing:.5px}
.hero p{left:127px;top:236px;width:470px;color:var(--white);font-size:16px;line-height:28px}
.hero .btn-yellow{left:127px;top:361px;width:262px;height:42px;font-size:14px}
.arrow{width:36px;height:36px;border-radius:50%;background:rgba(0,0,0,.45);display:flex;align-items:center;justify-content:center}

/* welcome */
.welcome-photo{left:135px;top:865px;width:350px;height:350px;border-radius:50%;border:8px solid var(--white);box-shadow:0 0 0 3px var(--teal);background:radial-gradient(circle at 45% 45%,#d9dde2,#8c969f 70%,#5d6670)}
.welcome h3{font-size:32px;font-weight:500;color:var(--teal)}
.welcome h2{font-size:40px;font-weight:700;color:var(--ink);line-height:50px}
.welcome-copy{left:530px;top:855px}
.welcome-text{left:530px;top:955px;width:530px}
.welcome-text p{margin-bottom:16px;font-size:14.5px}

/* eyecare */
.eyecare{left:0;top:1312px;width:1200px;height:533px;background:linear-gradient(90deg,#e4e9ef 0%,#eef1f5 45%,#dfe6ee 100%)}
.eyecare-photo{left:530px;top:0;width:670px;height:533px;background:linear-gradient(90deg,rgba(238,241,245,0) 0%,#c8d3df 30%,#9fb0c2 100%)}
.section-title{font-size:38px;font-weight:700;color:var(--ink);letter-spacing:.5px}
.eyecare h2{left:142px;top:76px}
.eyecare p{left:142px;top:148px;width:470px;font-size:14.5px}
.btn-outline{border:2px solid currentColor;border-radius:24px;font-size:15px;display:flex;align-items:center;justify-content:center}
.eyecare .btn-outline{left:142px;top:306px;width:212px;height:42px;color:var(--teal)}

.blue-band{left:0;top:1845px;width:1200px;height:793px;background:linear-gradient(180deg,#2e6ab4,#2a5ca4)}
.card{top:1764px;width:211px;height:316px;background:var(--white);box-shadow:0 6px 18px rgba(0,0,0,.15);text-align:center;padding:30px 16px 0}
.card svg{margin:0 auto;display:block}
.card h4{font-size:16px;font-weight:600;color:var(--ink);margin:26px 0 12px;text-transform:uppercase}
.card p{font-size:12.5px;line-height:22px;color:#555}

.myopia h2{left:142px;top:2196px;color:var(--white)}
.myopia p{left:142px;top:2266px;width:490px;color:var(--white);font-size:14.5px}
.myopia .btn-outline{left:142px;top:2460px;width:155px;height:44px;color:var(--white)}
.myopia-photo{left:708px;top:2140px;width:344px;height:344px;border-radius:50%;border:6px solid var(--white);background:radial-gradient(circle at 45% 50%,#e85a8a 0,#9e3c78 20%,#2b4f86 50%,#0f2c55 100%)}

/* blog */
.blog h2{left:0;top:2725px;width:1200px;text-align:center}
.post{top:2834px;width:283px;text-align:center}
.post-photo{height:181px;width:283px}
.post-date{display:inline-flex;align-items:center;gap:6px;background:var(--navy);color:var(--white);font-size:12px;font-weight:600;padding:0 18px;height:32px;border-radius:18px;margin-top:-16px;position:relative}
.post h5{font-size:14px;font-weight:600;color:var(--ink);margin:18px 0 8px}
.post p{font-size:12.5px;line-height:20px;color:#555;padding:0 10px}
.post .chev{margin-top:14px}

/* testimonials */
.testimonials{left:0;top:3295px;width:1200px;height:640px;background:linear-gradient(90deg,#c8d2d8 0%,#dde3e6 45%,#e9ecee 100%)}
.testi-photo{left:0;top:0;width:620px;height:640px;background:linear-gradient(90deg,#b7c5cd,#d6dde1 80%,rgba(233,236,238,0))}
.testimonials h2{left:633px;top:82px;font-size:36px}
.quote{width:320px}
.quote p{font-style:italic;font-size:14px;line-height:24px;color:#333}
.quote .who{font-style:italic;font-weight:500;font-size:15px;color:var(--ink);margin-top:4px}
.stars{color:var(--blue);font-size:15px;letter-spacing:3px}
.avatar{width:112px;height:112px;border-radius:50%;border:5px solid var(--white);background:linear-gradient(135deg,#d8c2ae,#9a806c)}
.q-mark{width:34px;height:34px;border-radius:50%;background:var(--blue);color:var(--white);font-size:26px;font-weight:700;display:flex;align-items:center;justify-content:center;line-height:1}

/* footer */
.footer{left:0;top:3890px;width:1200px;height:633px;background:var(--footer);color:var(--white)}
.footer h6{font-size:16px;font-weight:600;text-transform:uppercase;letter-spacing:.3px}
.footer h6::after{content:"";display:block;width:56px;height:2px;background:var(--white);margin-top:18px}
.field{left:127px;width:361px;height:34px;border:1px solid #bbb;font-size:12px;color:#ddd;padding:8px 8px}
.submit{left:127px;top:4293px;width:175px;height:34px;background:var(--yellow);color:var(--ink);font-weight:700;font-size:14px;display:flex;align-items:center;justify-content:center}
.info{display:flex;gap:14px;align-items:flex-start;font-size:13.5px;line-height:21px;color:#eee}
.ic{width:36px;height:36px;border-radius:50%;border:1px solid #ccc;flex:none;display:flex;align-items:center;justify-content:center}
.social{width:34px;height:34px;border-radius:50%;border:1px solid #ccc}
.rule{left:127px;top:4408px;width:946px;height:1px;background:#444}
.copyright{left:0;top:4455px;width:1200px;text-align:center;font-size:13px;color:#ddd}
</style>
</head>
<body>

<header class="abs header">
  <div class="abs logo"><span class="logo-box"></span><span class="logo-name">LUMAVUE<br>OPTOMETRY</span></div>
  <div class="abs call">
    <span class="call-icon"><svg width="20" height="20" viewBox="0 0 24 24"><path fill="#2f74bd" d="M6.6 10.8a15 15 0 0 0 6.6 6.6l2.2-2.2c.3-.3.7-.4 1-.2 1.1.4 2.3.6 3.6.6.6 0 1 .4 1 1V20c0 .6-.4 1-1 1A17 17 0 0 1 3 4c0-.6.4-1 1-1h3.5c.6 0 1 .4 1 1 0 1.3.2 2.5.6 3.6.1.3 0 .7-.2 1z"/></svg></span>
    <div><small>Call Now</small><strong>555-204-7310</strong></div>
  </div>
  <div class="abs btn-yellow"><svg width="14" height="14" viewBox="0 0 24 24"><path fill="#1f1f1f" d="M3 17.2V21h3.8L18 9.8 14.2 6zM20.7 7.1a1 1 0 0 0 0-1.4l-2.4-2.4a1 1 0 0 0-1.4 0l-1.8 1.8 3.8 3.8z"/></svg>Make an Appointment</div>
</header>
<nav class="abs nav"><ul><li>Home</li><li>Our Team</li><li>Eyecare</li><li>Myopia Control Clinic</li><li>Dry Eye Clinic</li><li>Eyewear</li><li>Patient Center</li><li>Contact</li></ul></nav>

<section class="abs hero">
  <div class="abs hero-photo" role="img" aria-label="Close-up photograph of a blue eye with digital light effects"></div>
  <h1 class="abs">LUMAVUE OPTOMETRY</h1>
  <p class="abs">Sed ut perspiciatis unde omnis iste natus voluptatem accusantium doloremque laudantium, totam rem aperiam, eaque ipsa quae ab illo inventore</p>
  <div class="abs btn-yellow"><svg width="14" height="14" viewBox="0 0 24 24"><path fill="#1f1f1f" d="M3 17.2V21h3.8L18 9.8 14.2 6zM20.7 7.1a1 1 0 0 0 0-1.4l-2.4-2.4a1 1 0 0 0-1.4 0l-1.8 1.8 3.8 3.8z"/></svg>Make an Appointment</div>
  <div class="abs arrow" style="left:56px;top:246px"><svg width="12" height="12" viewBox="0 0 12 12"><path d="M8 1 3 6l5 5" stroke="#fff" stroke-width="2" fill="none"/></svg></div>
  <div class="abs arrow" style="left:1104px;top:246px"><svg width="12" height="12" viewBox="0 0 12 12"><path d="m4 1 5 5-5 5" stroke="#fff" stroke-width="2" fill="none"/></svg></div>
  <svg class="abs" style="left:0;top:503px" width="1200" height="170" viewBox="0 0 1200 170" preserveAspectRatio="none">
    <path d="M0 130 C 250 20, 650 40, 1200 60 L1200 170 L0 170Z" fill="#f6c515"/>
    <path d="M0 150 C 260 50, 650 65, 1200 80 L1200 170 L0 170Z" fill="#2a5fa6"/>
    <path d="M0 165 C 270 75, 650 92, 1200 100 L1200 170 L0 170Z" fill="#fff"/>
  </svg>
</section>

<section class="welcome">
  <div class="abs welcome-photo" role="img" aria-label="Photograph of an optometry examination instrument"></div>
  <div class="abs welcome-copy"><h3>Welcome to</h3><h2>Lumavue Optometry</h2></div>
  <div class="abs welcome-text">
    <p>Where your vision and eye health are our sole priority. We take great pride in providing you with state-of-the-art eyecare matched with personal attention from our staff and doctors. Your quality of life is our goal and we believe that healthy eyesight is vital to achieving it.</p>
    <p>Our professional and personable staff is highly trained in helping you achieve and maintain healthy eyesight. Our optometrists have combined experiences and specialize in Orthokeratology (OrthoK), Ocular disease, Glaucoma diagnosis &amp; management.</p>
  </div>
</section>

<section class="abs eyecare">
  <div class="abs eyecare-photo" role="img" aria-label="Photograph of a smiling patient wearing a trial frame during an eye exam with an optometrist"></div>
  <h2 class="abs section-title">EYECARE</h2>
  <p class="abs">Sed ut perspiciatis unde omnis iste natus error sit voluptatem accusantium doloremque laudantium, totam rem aperiam, eaque ipsa quae ab illo inventore veritatis et quasi architecto beatae</p>
  <div class="abs btn-outline">View More Services</div>
</section>

<div class="abs blue-band"></div>

<div class="abs card" style="left:145px">
  <svg width="60" height="60" viewBox="0 0 60 60" fill="none" stroke="#f6c515" stroke-width="2.5"><path d="M4 30c8-12 16-18 26-18s18 6 26 18c-8 12-16 18-26 18S12 42 4 30z"/><circle cx="30" cy="30" r="9"/><path d="M4 8V4h4M52 4h4v4M56 52v4h-4M8 56H4v-4"/></svg>
  <h4>Vision Services</h4>
  <p>Sed ut perspiciatis unde omnis iste natus error sit voluptatem accusantium doloremque uts, totam rem aperiam, eaque</p>
</div>
<div class="abs card" style="left:380px">
  <svg width="60" height="60" viewBox="0 0 60 60" fill="none" stroke="#f6c515" stroke-width="2.5"><rect x="16" y="6" width="34" height="44" rx="2"/><path d="M24 16h18M26 24h14M28 32h10M30 40h6"/><path d="M6 54 20 40"/><circle cx="22" cy="38" r="5"/></svg>
  <h4>Eye Exams</h4>
  <p>Sed ut perspiciatis unde omnis iste natus error sit voluptatem accusantium doloremque uts, totam rem aperiam, eaque</p>
</div>
<div class="abs card" style="left:612px">
  <svg width="60" height="60" viewBox="0 0 60 60" fill="none" stroke="#f6c515" stroke-width="2.5"><path d="M4 30c8-12 16-18 26-18s18 6 26 18c-8 12-16 18-26 18S12 42 4 30z"/><circle cx="30" cy="30" r="10"/><circle cx="30" cy="30" r="4"/><path d="M30 2v8M30 50v8M2 30h6M52 30h6"/></svg>
  <h4>Glaucoma</h4>
  <p>Sed ut perspiciatis unde omnis iste natus error sit voluptatem accusantium doloremque uts, totam rem aperiam, eaque</p>
</div>
<div class="abs card" style="left:844px">
  <svg width="60" height="60" viewBox="0 0 60 60" fill="none" stroke="#f6c515" stroke-width="2.5"><rect x="16" y="4" width="28" height="38" rx="4"/><rect x="21" y="10" width="18" height="12"/><path d="M24 30h12M24 36h12M30 42v8M30 50c0 4 6 6 6 0"/></svg>
  <h4>Diabites</h4>
  <p>Sed ut perspiciatis unde omnis iste natus error sit voluptatem accusantium doloremque uts, totam rem aperiam, eaque</p>
</div>

<section class="myopia">
  <h2 class="abs section-title">MYOPIA CONTROL CLINIC</h2>
  <p class="abs">Sed ut perspiciatis unde omnis iste natus error sit voluptatem accusantium doloremque laudantium, totam rem aperiam, eaque ipsa quae ab illo inventore veritatis et quasi architecto beatae vitae dicta sunt explicabo. Nemo enim ipsam voluptatem quia voluptas sit aspernatur aut odit aut fugit, sed</p>
  <div class="abs btn-outline">Read More</div>
  <div class="abs myopia-photo" role="img" aria-label="Illustration of an eyeball cross-section showing the lens and retina"></div>
</section>

<section class="blog">
  <h2 class="abs section-title">LATEST BLOG</h2>
  <article class="abs post" style="left:145px">
    <div class="post-photo" role="img" aria-label="Photograph of a woman's eye beside an eye chart" style="background:linear-gradient(90deg,#c9a98f,#e8e4df 60%,#f2f2f2)"></div>
    <span class="post-date"><svg width="11" height="11" viewBox="0 0 12 12"><rect x="1" y="2" width="10" height="9" fill="none" stroke="#fff"/><path d="M1 5h10" stroke="#fff"/></svg>OCTOBER 17, 2019</span>
    <h5>QUIS AUTEM VEL EUM IURE</h5>
    <p>Sed ut perspiciatis unde omnis iste natus error sit voluptatem accusantium doloremque lautium, totam rem aperiam</p>
    <svg class="chev" width="16" height="16" viewBox="0 0 16 16" fill="none" stroke="#222" stroke-width="1.6"><path d="m3 3 5 5 5-5M3 9l5 5 5-5"/></svg>
  </article>
  <article class="abs post" style="left:458px">
    <div class="post-photo" role="img" aria-label="Photograph of a phoropter used in eye examinations" style="background:linear-gradient(135deg,#9aa0a6,#d6d8da 55%,#767c82)"></div>
    <span class="post-date"><svg width="11" height="11" viewBox="0 0 12 12"><rect x="1" y="2" width="10" height="9" fill="none" stroke="#fff"/><path d="M1 5h10" stroke="#fff"/></svg>OCTOBER 17, 2019</span>
    <h5>QUIS AUTEM VEL EUM IURE</h5>
    <p>Sed ut perspiciatis unde omnis iste natus error sit voluptatem accusantium doloremque lautium, totam rem aperiam</p>
    <svg class="chev" width="16" height="16" viewBox="0 0 16 16" fill="none" stroke="#222" stroke-width="1.6"><path d="m3 3 5 5 5-5M3 9l5 5 5-5"/></svg>
  </article>
  <article class="abs post" style="left:772px">
    <div class="post-photo" role="img" aria-label="Photograph of eyeglasses resting on a table against an autumn background" style="background:linear-gradient(180deg,#8a7a4e,#b59a5c 55%,#6f5a3a)"></div>
    <span class="post-date"><svg width="11" height="11" viewBox="0 0 12 12"><rect x="1" y="2" width="10" height="9" fill="none" stroke="#fff"/><path d="M1 5h10" stroke="#fff"/></svg>OCTOBER 17, 2019</span>
    <h5>QUIS AUTEM VEL EUM IURE</h5>
    <p>Sed ut perspiciatis unde omnis iste natus error sit voluptatem accusantium doloremque lautium, totam rem aperiam</p>
    <svg class="chev" width="16" height="16" viewBox="0 0 16 16" fill="none" stroke="#222" stroke-width="1.6"><path d="m3 3 5 5 5-5M3 9l5 5 5-5"/></svg>
  </article>
</section>

<section class="abs testimonials">
  <div class="abs testi-photo" role="img" aria-label="Photograph of a smiling woman adjusting her glasses"></div>
  <h2 class="abs section-title">TESTIMONIALS</h2>
  <div class="abs avatar" style="left:631px;top:182px" role="img" aria-label="Portrait of a patient"></div>
  <div class="abs q-mark" style="left:718px;top:176px">&ldquo;</div>
  <div class="abs quote" style="left:772px;top:196px">
    <p>Sed ut perspiciatis unde omnis iste natus error sit voluptatem accusantium loremque laudantium, totam rem aperiam</p>
    <div class="who">John Doe - &nbsp;Patient, Alderbrook</div>
    <div class="stars">★★★★★</div>
  </div>
  <div class="abs avatar" style="left:637px;top:372px" role="img" aria-label="Portrait of a patient"></div>
  <div class="abs q-mark" style="left:724px;top:366px">&ldquo;</div>
  <div class="abs quote" style="left:772px;top:366px">
    <p>Sed ut perspiciatis unde omnis iste natus error sit voluptatem accusantium loremque laudantium, totam rem aperiam</p>
    <div class="who">John Doe - &nbsp;Patient, Alderbrook</div>
    <div class="stars">★★★★★</div>
  </div>
</section>

<footer class="abs footer">
  <svg class="abs" style="left:0;top:-90px" width="1200" height="110" viewBox="0 0 1200 110" preserveAspectRatio="none">
    <path d="M0 60 C 300 120, 800 -10, 1200 20 L1200 110 L0 110Z" fill="#f6c515"/>
    <path d="M0 70 C 300 130, 800 5, 1200 40 L1200 110 L0 110Z" fill="#2a5fa6"/>
    <path d="M0 88 C 300 140, 800 25, 1200 62 L1200 110 L0 110Z" fill="#0d0d0d"/>
  </svg>
  <h6 class="abs" style="left:127px;top:92px">Make an Appointment</h6>
  <h6 class="abs" style="left:549px;top:92px">Lumavue Optometry</h6>
  <h6 class="abs" style="left:811px;top:92px">Kestrel Point</h6>
</footer>

<div class="abs field" style="top:4076px">First Name</div>
<div class="abs field" style="top:4121px">Email Address</div>
<div class="abs field" style="top:4166px">Phone Number</div>
<div class="abs field" style="top:4211px;height:62px">Message</div>
<div class="abs submit">SUBMIT</div>

<div class="abs info" style="left:549px;top:4070px;width:230px"><span class="ic"><svg width="14" height="16" viewBox="0 0 24 24"><path fill="#fff" d="M12 2a7 7 0 0 0-7 7c0 5 7 13 7 13s7-8 7-13a7 7 0 0 0-7-7zm0 9.5A2.5 2.5 0 1 1 12 6a2.5 2.5 0 0 1 0 5.5z"/></svg></span><span>4120 Marrow Lane,<br>Alderbrook, CA 90000</span></div>
<div class="abs info" style="left:549px;top:4135px;width:230px"><span class="ic"><svg width="14" height="14" viewBox="0 0 24 24"><path fill="#fff" d="M6.6 10.8a15 15 0 0 0 6.6 6.6l2.2-2.2c.3-.3.7-.4 1-.2 1.1.4 2.3.6 3.6.6.6 0 1 .4 1 1V20c0 .6-.4 1-1 1A17 17 0 0 1 3 4c0-.6.4-1 1-1h3.5c.6 0 1 .4 1 1 0 1.3.2 2.5.6 3.6.1.3 0 .7-.2 1z"/></svg></span><span>Phone: 555-204-7310<br>Fax: 555-204-7370</span></div>
<div class="abs info" style="left:549px;top:4200px;width:240px"><span class="ic"><svg width="14" height="12" viewBox="0 0 24 20"><rect x="1" y="1" width="22" height="18" fill="none" stroke="#fff" stroke-width="2"/><path d="m1 1 11 9 11-9" fill="none" stroke="#fff" stroke-width="2"/></svg></span><span>Email:<br>info@brivaloka.com</span></div>
<div class="abs" style="left:566px;top:4283px;display:flex;gap:10px"><span class="social"></span><span class="social"></span><span class="social"></span></div>

<div class="abs info" style="left:811px;top:4070px;width:260px"><span class="ic"><svg width="14" height="16" viewBox="0 0 24 24"><path fill="#fff" d="M12 2a7 7 0 0 0-7 7c0 5 7 13 7 13s7-8 7-13a7 7 0 0 0-7-7zm0 9.5A2.5 2.5 0 1 1 12 6a2.5 2.5 0 0 1 0 5.5z"/></svg></span><span>2087 Linden Ave,<br>Suite 4, Kestrel Point, CA 90010</span></div>
<div class="abs info" style="left:811px;top:4135px;width:230px"><span class="ic"><svg width="14" height="14" viewBox="0 0 24 24"><path fill="#fff" d="M6.6 10.8a15 15 0 0 0 6.6 6.6l2.2-2.2c.3-.3.7-.4 1-.2 1.1.4 2.3.6 3.6.6.6 0 1 .4 1 1V20c0 .6-.4 1-1 1A17 17 0 0 1 3 4c0-.6.4-1 1-1h3.5c.6 0 1 .4 1 1 0 1.3.2 2.5.6 3.6.1.3 0 .7-.2 1z"/></svg></span><span>Phone:<br>555-318-6020</span></div>
<div class="abs info" style="left:811px;top:4200px;width:270px"><span class="ic"><svg width="14" height="12" viewBox="0 0 24 20"><rect x="1" y="1" width="22" height="18" fill="none" stroke="#fff" stroke-width="2"/><path d="m1 1 11 9 11-9" fill="none" stroke="#fff" stroke-width="2"/></svg></span><span>Email:<br>kestrelpoint@brivaloka.com</span></div>

<div class="abs rule"></div>
<div class="abs copyright">© Copyright 2019 Lumavue Optometry. All Rights Reserved.</div>

</body>
</html>
```